Dovin Sound 862 the new wave for sound to enlighten open ears

This is a music recording studio, we need pictures of a booth, random pictures of anything that will draw interest to a recording studio, we just need the website to reflect a music studio recording website. Apply generic information on the site that correlates with most music studio websites up to date. We want the modern style look that will entice eyes across the nation. Information should be easily accessible on the website. Dovin Sound 862 is owned by Marcellus Okafor located 5176 Bellweather Ln, Corvane, Fl, 33027. Email: Mokaforsound@quillnestmail.net and best contact number to date is 417-293-7041. The sound coming out of this location will be radio ready at all times, artist come in one way and come out with more wisdom than before. Its the new way to make music the appropriate way and bring the best out of those willing to reach their peak.

Target Market(s)

Recording Artist

Industry/Entity Type

Recording Studio

Coding

Coded - Design and coding required

Number of Pages Required

1 page

Font styles to use
Sans Serif

Requirements
Must have
• Anything that gives the site a music feel
Nice to have
• microphones, booths, studio mixing desk

```html
<!DOCTYPE html>
<html lang="en">
<head>
<meta charset="utf-8">
<title>Dovin Sound 862</title>
<link rel="stylesheet" href="https://fonts.googleapis.com/css2?family=Roboto:wght@400;500;700&family=Roboto+Slab:wght@400;700&display=swap">
<style>
:root{
  --red:#c6363a;
  --red-dark:#a92a2e;
  --ink:#f2f2f2;
  --muted:#cfcfcf;
  --bg:#1d1d1d;
  --bg-deep:#141414;
  --bg-foot:#101010;
  --card:#f8eaea;
  --card-ink:#4a4a4a;
}
*{margin:0;padding:0;box-sizing:border-box}
html,body{width:1200px;height:2517px;overflow:hidden}
body{position:relative;background:var(--bg);font-family:'Roboto',sans-serif;color:var(--ink)}
.abs{position:absolute}
.brand{display:flex;align-items:center;gap:14px}
.brand-dot{width:26px;height:26px;border-radius:50%;background:var(--red)}
.brand-name{font-family:'Roboto',sans-serif;font-weight:700;font-size:24px;color:#fff;letter-spacing:.3px}

/* header */
.site-header{left:0;top:0;width:1200px;height:117px;background:var(--bg-deep)}
.site-header .brand{position:absolute;left:86px;top:45px}
.main-nav{position:absolute;right:88px;top:50px;display:flex;gap:40px;font-size:14px;font-weight:400;text-transform:uppercase}
.main-nav a{color:#fff;text-decoration:none}
.main-nav a.active{color:var(--red);display:flex;align-items:center;gap:8px}
.main-nav a.active::before{content:"";width:12px;height:12px;border-radius:50%;background:var(--red)}

/* hero */
.hero{left:0;top:117px;width:1200px;height:474px;background:radial-gradient(ellipse at 50% 60%,#6b4a2c 0%,#3d2a1b 40%,#1b1410 80%)}
.hero-title{position:absolute;left:86px;top:160px;font-family:'Roboto Slab',serif;font-size:46px;font-weight:400;color:#fff;letter-spacing:1px}
.hero-dots{position:absolute;left:556px;top:424px;display:flex;gap:6px}
.hero-dots span{width:12px;height:12px;border-radius:50%;border:1.5px solid #fff}
.hero-dots span.on{background:#fff}

/* section title */
.section-title{position:absolute;left:0;width:1200px;display:flex;justify-content:center;align-items:center;gap:10px;font-family:'Roboto Slab',serif;font-size:27px;font-weight:400;color:var(--red);text-transform:uppercase}
.section-title::before{content:"";width:16px;height:16px;border-radius:50%;background:var(--red)}

/* vision */
.vision{left:0;top:591px;width:1200px;height:345px;background:#1c1c1c}
.vision-text{position:absolute;left:205px;top:116px;width:790px;text-align:center;font-size:13px;line-height:21px;color:#e8e8e8}
.btn{position:absolute;background:var(--red);color:#fff;font-size:13px;text-transform:uppercase;display:flex;align-items:center;justify-content:center;border-radius:3px}
.vision .btn{left:545px;top:231px;width:110px;height:39px}

/* services */
.services{left:0;top:936px;width:1200px;height:497px;background:linear-gradient(90deg,#1a0f0f 0%,#2a1a18 35%,#1c1414 65%,#120c0c 100%)}
.services-frame{position:absolute;left:12px;top:10px;width:1176px;height:477px;border:1px dashed var(--red)}
.service{position:absolute;top:166px;width:260px;text-align:center}
.service-photo{width:174px;height:174px;margin:0 auto;border-radius:50%;border:3px solid var(--red);position:relative;overflow:hidden}
.service-photo .band{position:absolute;left:0;bottom:0;width:100%;height:56px;background:rgba(198,54,58,.85);font-size:18px;font-weight:500;color:#fff;padding-top:12px;text-transform:uppercase}
.service p{margin-top:20px;font-size:13px;line-height:18px;color:#eee}
.service .more{margin-top:8px;font-size:12px;color:var(--red);text-transform:uppercase;display:flex;justify-content:center;align-items:center;gap:6px}
.slider-arrow{position:absolute;top:272px}

/* pricing */
.pricing{left:0;top:1433px;width:1200px;height:728px;background:#1e1e1e}
.pricing-text{position:absolute;left:250px;top:121px;width:700px;text-align:center;font-size:13px;line-height:20px;color:#e8e8e8}
.plan{position:absolute;background:var(--card);box-shadow:0 4px 12px rgba(0,0,0,.5)}
.plan-head{position:relative;height:62px;background:var(--red);color:#fff;font-size:17px;font-weight:500;text-align:center;text-transform:uppercase;line-height:27px;padding-top:8px}
.plan-head svg{position:absolute;left:0;top:61px;display:block}
.plan ul{list-style:none;margin-top:34px}
.plan li{height:50px;display:flex;align-items:center;justify-content:center;font-size:15px;color:var(--card-ink)}
.plan li.hi{background:var(--red);color:#fff}
.plan .subscribe{height:42px;background:var(--red);color:#fff;font-weight:700;font-size:16px;display:flex;align-items:center;justify-content:center;text-transform:uppercase}
.plan.featured .plan-head{height:70px;padding-top:12px}
.plan.featured .plan-head svg{top:69px}
.plan.featured li{height:57px;font-size:16px}

/* footer */
.site-footer{left:0;top:2161px;width:1200px;height:306px;background:linear-gradient(180deg,#121212,#1a1a1a)}
.foot-col{position:absolute;top:68px}
.foot-title{font-size:15px;font-weight:500;color:#fff;text-transform:uppercase;margin-bottom:16px}
.foot-about{font-size:13px;line-height:19px;color:#e6e6e6;width:230px;margin-top:18px}
.social{display:flex;gap:10px;margin-top:20px}
.social span{width:36px;height:36px;border-radius:50%;border:2px solid #fff}
.contact-list{list-style:none;font-size:12.5px;color:#e6e6e6}
.contact-list li{display:flex;align-items:center;gap:16px;height:44px}
.link-list{list-style:none;font-size:12.5px;color:#e6e6e6}
.link-list li{height:27.5px;display:flex;align-items:center;gap:10px}
.link-list li::before{content:"»";color:#fff;font-size:13px}
.copyright{left:0;top:2467px;width:1200px;height:50px;background:#0c0c0c;color:#ddd;font-size:13px;display:flex;align-items:center;justify-content:center}
</style>
</head>
<body>

<header class="site-header abs">
  <div class="brand"><span class="brand-dot"></span><span class="brand-name">DOVIN SOUND 862</span></div>
  <nav class="main-nav">
    <a class="active" href="#">Home</a><a href="#">Studio</a><a href="#">Equipment</a><a href="#">Rates &amp; Services</a><a href="#">Contacts</a>
  </nav>
</header>

<section class="hero abs" role="img" aria-label="Recording studio control room with a large mixing desk and monitors">
  <h1 class="hero-title">DOVIN SOUND 862</h1>
  <div class="hero-dots"><span class="on"></span><span></span><span></span><span></span><span></span></div>
</section>

<section class="vision abs">
  <h2 class="section-title" style="top:68px">Our Vision</h2>
  <p class="vision-text">Lorem Ipsum is simply dummy text of the printing and typesetting industry. Lorem Ipsum has been the industry's standard dummy text ever since the 1500s, when an unknown printer took a galley of type and scrambled it to make a type specimen book. It has survived not only five centuries, but also the leap into electronic typesetting, remaining essentially unchanged. Iwith desktop publishing software like Verdant LayoutKit including versions of Lorem Ipsum.</p>
  <a class="btn">Read More</a>
</section>

<section class="services abs" role="img" aria-label="Dim studio background with an engineer at a mixing console">
  <div class="services-frame"></div>
  <h2 class="section-title" style="top:76px">Our Services</h2>
  <svg class="slider-arrow" style="left:86px" width="14" height="26" viewBox="0 0 14 26"><path d="M12 2 2 13l10 11" fill="none" stroke="#bbb" stroke-width="2"/></svg>
  <svg class="slider-arrow" style="left:1100px" width="14" height="26" viewBox="0 0 14 26"><path d="M2 2l10 11-10 11" fill="none" stroke="#bbb" stroke-width="2"/></svg>
  <div class="service" style="left:132px">
    <div class="service-photo" role="img" aria-label="Artists working in the studio" style="background:linear-gradient(135deg,#5a4a44,#2c2624)"><div class="band">Studio</div></div>
    <p>It is a long established will distracted<br>by the readable page</p>
    <div class="more">Read More <svg width="12" height="12" viewBox="0 0 12 12"><circle cx="6" cy="6" r="6" fill="#c6363a"/><path d="M5 3l3 3-3 3" fill="none" stroke="#1a1010" stroke-width="1.6"/></svg></div>
  </div>
  <div class="service" style="left:469px">
    <div class="service-photo" role="img" aria-label="Studio staff member at a workstation" style="background:linear-gradient(135deg,#8a9aa8,#3e4a55)"><div class="band">Staff</div></div>
    <p>It is a long established will distracted<br>by the readable page</p>
    <div class="more">Read More <svg width="12" height="12" viewBox="0 0 12 12"><circle cx="6" cy="6" r="6" fill="#c6363a"/><path d="M5 3l3 3-3 3" fill="none" stroke="#1a1010" stroke-width="1.6"/></svg></div>
  </div>
  <div class="service" style="left:810px">
    <div class="service-photo" role="img" aria-label="Close view of studio mixing equipment" style="background:linear-gradient(135deg,#7a6a5a,#2e2a28)"><div class="band">Equipment</div></div>
    <p>It is a long established will distracted<br>by the readable page</p>
    <div class="more">Read More <svg width="12" height="12" viewBox="0 0 12 12"><circle cx="6" cy="6" r="6" fill="#c6363a"/><path d="M5 3l3 3-3 3" fill="none" stroke="#1a1010" stroke-width="1.6"/></svg></div>
  </div>
</section>

<section class="pricing abs">
  <h2 class="section-title" style="top:70px">Pricing Table</h2>
  <p class="pricing-text">Lorem Ipsum is simply dummy text of the printing and typesetting industry. Lorem Ipsum has been the industry's<br>standard dummy text ever&nbsp; Verdant LayoutKit including versions of Lorem Ipsum.</p>

  <div class="plan" style="left:185px;top:235px;width:253px">
    <div class="plan-head">Recording<br>Price<svg width="253" height="28" viewBox="0 0 253 28"><path d="M0 0h253L126.5 28z" fill="#c6363a"/></svg></div>
    <ul>
      <li>$80 / hr min 4 hrs req</li><li class="hi">$75 / hr min 8 hrs req</li><li>$70 / hr min 12 hrs req</li><li class="hi">$90 for individual hrs</li><li>Packages recommended</li>
    </ul>
    <div class="subscribe">Subscribe Now !</div>
  </div>

  <div class="plan featured" style="left:461px;top:216px;width:279px">
    <div class="plan-head">Memberships<br>Deals<svg width="279" height="32" viewBox="0 0 279 32"><path d="M0 0h279L139.5 32z" fill="#c6363a"/></svg></div>
    <ul>
      <li>$1500,Get 48 hrs,24 hrs mix</li><li class="hi">$2500,Get 72 hrs,48 hrs mix</li><li>$3500,Get 96 hrs,72 hrs mix</li><li class="hi">$90 for Membership Deals</li><li>Packages recommended</li>
    </ul>
    <div class="subscribe" style="height:48px">Subscribe Now !</div>
  </div>

  <div class="plan" style="left:763px;top:235px;width:252px">
    <div class="plan-head">Recording<br>Price<svg width="252" height="28" viewBox="0 0 252 28"><path d="M0 0h252L126 28z" fill="#c6363a"/></svg></div>
    <ul>
      <li>$50 / hr min 4 hrs req</li><li class="hi">$45 / hr min 8 hrs req</li><li>$40 / hr min 12 hrs req</li><li class="hi">$60 for individual hrs</li><li>Packages recommended</li>
    </ul>
    <div class="subscribe">Subscribe Now !</div>
  </div>
</section>

<footer class="site-footer abs">
  <div class="foot-col" style="left:106px;top:62px">
    <div class="brand"><span class="brand-dot"></span><span class="brand-name" style="font-size:20px">DOVIN SOUND 862</span></div>
    <p class="foot-about">Many desktop publishing packages and web page editors now use , and a search for 'lorem ipsum</p>
    <div class="social" aria-label="Social links"><span></span><span></span><span></span><span></span></div>
  </div>
  <div class="foot-col" style="left:430px">
    <div class="foot-title">Contact Us</div>
    <ul class="contact-list">
      <li><svg width="16" height="16" viewBox="0 0 16 16"><path d="M8 1a5 5 0 0 1 5 5c0 4-5 9-5 9S3 10 3 6a5 5 0 0 1 5-5z" fill="#fff"/><circle cx="8" cy="6" r="2" fill="#121212"/></svg>5176 Bellweather Ln, Corvane, Fl, 33027</li>
      <li><svg width="16" height="16" viewBox="0 0 16 16"><rect x="4" y="1" width="8" height="14" rx="1.5" fill="none" stroke="#fff" stroke-width="1.5"/><circle cx="8" cy="12.5" r="1" fill="#fff"/></svg>Call Us : 417-293-7041</li>
      <li><svg width="16" height="16" viewBox="0 0 16 16"><rect x="1.5" y="3.5" width="13" height="9" fill="none" stroke="#fff" stroke-width="1.4"/><path d="M1.5 3.5 8 9l6.5-5.5" fill="none" stroke="#fff" stroke-width="1.4"/></svg>Mokaforsound@quillnestmail.net</li>
    </ul>
  </div>
  <div class="foot-col" style="left:757px">
    <div class="foot-title">Menus</div>
    <ul class="link-list"><li>Home</li><li>Studio</li><li>Equipment</li><li>Rates &amp; Services</li><li>Contacts</li></ul>
  </div>
  <div class="foot-col" style="left:956px">
    <div class="foot-title">Other Links</div>
    <ul class="link-list"><li>Terms and conditions</li><li>Privacy policy</li><li>Sitemap</li><li>Solutions</li><li>Customer Support</li></ul>
  </div>
</footer>

<div class="copyright abs">@copyright 2017 Dovin Sound 862.All Rights Reserved</div>

</body>
</html>
```